Equipment Finance Specialist I work with companies who need the funds to buy their equipment

I would like a business card that stands out on the shelves. I want to be able to hand it to someone and say WOW. This card should have my logo.
You can put color into it I am very open on design and color

What my company does is we deal with dealerships that sell equipment such as Dump Trucks garbage trucks tractors trailers. Customers get referred to us and depending on their time in business we will ask for the following items

Companies that have been in business for more than two years we have a credit application program up to 250K . With this program we need the following items Credit application filled out(which is what I would like to be able for the customer to click on my website to get.) as well as three current month bank statements.

Deals over 250k we will need the following items

2 years business tax returns
2 years personal tax returns
Profit & Loss statement
Personal Financial Statement

what we do
100% FINANCING
SEASONAL PAYMENTS
LOAN BALLOON PAYMENTS
TRAC LEASING
LOW-INTEREST REFINANCING RATES
DEBT CONSOLIDATION

We specialize in creative financing solutions and offer a variety of reliable, flexible and expandable lending choices.

Target Market(s)

Trucking Companies

Industry/Entity Type

Trucking Company

Contact Information for Business Card

* $250,000 Application only Program
* Loans from $30,000 to 5,000,000
* Competitive Interest Rates

Font styles to use
Serif
Sans Serif

Colors

Designer to choose colors to be used in the design.

Requirements
Must have
• On the back of the card.
• * $250,000 Application only Program
• * Loans from $30,000 to 5,000,000
• My name, email, website. address
• * Competitive Interest Rates
• * 100% Financing
Nice to have
• I want my logo to pop on the card
• My logo is the great one I would like to use
Should not have
• I am up for your creativity as well

```html
<!DOCTYPE html>
<html lang="en">
<head>
<meta charset="utf-8">
<title>Brackton Lending – Business Card</title>
<link href="https://fonts.googleapis.com/css2?family=Open+Sans:wght@400;600;800&display=swap" rel="stylesheet">
<style>
  :root {
    --backdrop: #2a2b2e;
    --crimson: #e3134f;
    --crimson-deep: #bb0b3a;
    --navy: #1a2f7a;
    --navy-soft: #3a4f96;
    --paper: #ffffff;
    --ink: #3a3a3a;
    --red-accent: #d6153f;
  }
  * { box-sizing: border-box; margin: 0; padding: 0; }
  html, body { width: 1200px; height: 885px; overflow: hidden; }
  body {
    background: var(--backdrop);
    font-family: "Open Sans", Arial, sans-serif;
    position: relative;
  }
  .card {
    position: absolute;
    width: 600px;
    height: 343px;
    border-radius: 2px;
    overflow: hidden;
  }
  /* Front card */
  .card-front {
    left: 70px; top: 60px;
    background: linear-gradient(135deg, var(--crimson) 0%, var(--crimson-deep) 100%);
    color: var(--paper);
    text-align: center;
  }
  .brand-front {
    position: absolute;
    left: 0; right: 0; top: 92px;
    display: flex; align-items: center; justify-content: center; gap: 14px;
  }
  .brand-dot {
    width: 46px; height: 46px; border-radius: 50%;
    background: var(--paper);
    flex: none;
  }
  .brand-name {
    font-weight: 800; font-size: 32px; letter-spacing: 1px; white-space: nowrap;
  }
  .front-facts {
    position: absolute; left: 0; right: 0; bottom: 44px;
    font-size: 17px; line-height: 1.35;
  }
  /* Back card */
  .card-back {
    left: 530px; top: 482px;
    background: var(--paper);
  }
  .back-band {
    position: absolute; left: 0; top: 0;
    width: 100%; height: 14px;
    background: var(--navy);
  }
  .contact {
    position: absolute; left: 36px; top: 54px;
    color: var(--ink);
  }
  .contact-name {
    color: var(--navy); font-weight: 800; font-size: 24px; letter-spacing: 0.5px;
  }
  .contact-title {
    color: var(--red-accent); font-weight: 600; font-size: 15px; letter-spacing: 0.5px;
    margin-bottom: 14px;
  }
  .contact-line {
    font-size: 15px; font-weight: 600; line-height: 1.45; white-space: nowrap;
  }
  .crane-art {
    position: absolute; left: 300px; top: 90px;
    width: 300px; height: 253px;
    background: linear-gradient(160deg, var(--navy-soft) 0%, var(--navy) 100%);
    opacity: 0.9;
    clip-path: polygon(0 0, 100% 30%, 100% 100%, 20% 100%);
  }
  .brand-back {
    position: absolute; right: 28px; top: 32px;
    display: flex; align-items: center; gap: 10px;
  }
  .brand-back .brand-dot { width: 30px; height: 30px; background: var(--navy); }
  .brand-back .brand-name { color: var(--navy); font-size: 20px; }
</style>
</head>
<body>
  <section class="card card-front">
    <div class="brand-front">
      <span class="brand-dot"></span>
      <span class="brand-name">BRACKTON LENDING</span>
    </div>
    <p class="front-facts">
      $250,000 Application only Program &bull; Loans from $30,000 to 5,000,000<br>
      Competitive Interest Rates &bull; 100% Financing
    </p>
  </section>

  <section class="card card-back">
    <div class="back-band"></div>
    <div class="crane-art" role="img" aria-label="Illustration of a navy truck-mounted crane boom with hook"></div>
    <div class="brand-back">
      <span class="brand-dot"></span>
      <span class="brand-name">BRACKTON LENDING</span>
    </div>
    <div class="contact">
      <p class="contact-name">DORIAN KESSEL</p>
      <p class="contact-title">PRESIDENT</p>
      <p class="contact-line">4120 Quillon Avenue<br>Marrow Bend, NY 11020</p>
      <p class="contact-line">555 0142 7789</p>
      <p class="contact-line">dorian@bracktonlending.com</p>
      <p class="contact-line">www.bracktonlending.com</p>
    </div>
  </section>
</body>
</html>
```